Registration Page - Webinar

I need some proposition for a high conversion landing page for a Webinar.
This LP should follow some (minimal) rules:
1 - We need to have a registration box at it
2 - 1, 2 or 3 Keynote Speakers
3 - Featuring Time & Date
4 - All webinars will be free
5 - Title of the webinar
6 - Description of the webinar
7 - Should harmonize with my home page colors (www.themaplehearth.com)

```html
<!DOCTYPE html>
<html lang="en">
<head>
<meta charset="utf-8">
<title>The Maple Hearth – Webinar Registration</title>
<link href="https://fonts.googleapis.com/css2?family=Poppins:wght@400;500;600;700&display=swap" rel="stylesheet">
<style>
:root{
  --magenta:#e8066d;
  --orange:#f47a20;
  --teal:#21b3d3;
  --navy:#3a1f6b;
  --green:#1fbf3a;
  --dark:#262626;
  --white:#fff;
  --text:#333;
}
*{box-sizing:border-box;margin:0;padding:0}
html,body{width:983px;height:1200px;overflow:hidden}
body{font-family:'Poppins',sans-serif;background:var(--white);position:relative;color:var(--text)}
.abs{position:absolute}
/* nav */
.topnav{left:0;top:0;width:983px;height:41px;background:var(--magenta)}
.topnav a{position:absolute;top:10px;color:var(--white);font-size:11px;font-weight:500;text-decoration:none}
.social{position:absolute;top:14px;width:12px;height:12px;border-radius:50%;background:var(--white)}
/* header */
.header{left:0;top:41px;width:983px;height:72px;background:var(--white)}
.phone-pill{background:var(--green);color:var(--white);font-weight:600;display:flex;align-items:center;gap:6px;border-radius:2px}
.phone-pill svg{flex:none}
.phones{display:flex;gap:14px;font-size:10.5px;color:#444;align-items:center}
.phones span{display:flex;align-items:center;gap:4px}
.dot{width:10px;height:10px;border-radius:50%;display:inline-block}
.brand{text-align:center;font-weight:700;color:var(--magenta);line-height:1}
.brand small{display:block;color:var(--navy);letter-spacing:4px;font-weight:600}
.cta{display:flex;align-items:center;gap:6px;font-weight:600;color:var(--navy);line-height:1.05}
.cta .ic{border-radius:50%;display:flex;align-items:center;justify-content:center;flex:none}
/* hero */
.hero{left:0;top:113px;width:983px;height:449px;background:linear-gradient(100deg,#23374f 0%,#5a6673 35%,#8a6a4e 55%,#9a8d80 80%,#6f6a63 100%)}
.hero-shade{left:0;top:113px;width:983px;height:449px;background:linear-gradient(90deg,rgba(0,0,0,.35),rgba(0,0,0,0) 60%)}
.logo-notch{left:415px;top:100px;width:152px;height:40px;background:var(--white);border-radius:0 0 80px 80px/0 0 40px 40px}
.title{left:95px;top:236px;font-size:26px;font-weight:700;color:var(--white);line-height:1.22;text-transform:uppercase}
.pill{left:94px;width:247px;height:43px;border-radius:22px;background:linear-gradient(90deg,var(--orange),var(--magenta));display:flex;align-items:center;color:var(--white);font-weight:600;font-size:17px}
.pill .ic{width:34px;height:34px;border-radius:50%;background:var(--teal);margin:0 9px 0 5px;display:flex;align-items:center;justify-content:center}
.count{top:426px;width:58px;height:57px;border:1.5px solid var(--white);color:var(--white);text-align:center;font-weight:700}
.count b{display:block;font-size:27px;line-height:1.2;margin-top:2px}
.count span{display:block;font-size:12px;line-height:1}
.free-tab{left:103px;top:517px;width:212px;height:45px;background:#3b3b3b;border-radius:36px 36px 0 0;color:var(--white);font-weight:600;font-size:14px;padding:10px 0 0 30px}
.form{left:578px;top:163px;width:300px;height:345px;background:rgba(33,179,211,.9)}
.form h2{position:absolute;left:0;top:26px;width:100%;text-align:center;color:var(--white);font-size:19px;font-weight:700}
.field{position:absolute;left:27px;width:245px;height:34px;border:1.2px solid var(--white);color:var(--white);font-size:10.5px;padding:9px 0 0 16px}
.btn{position:absolute;left:27px;top:273px;width:245px;height:43px;background:var(--orange);color:var(--white);font-weight:700;font-size:14px;text-align:center;line-height:43px}
/* speakers */
.speakers{left:0;top:562px;width:983px;height:380px;background:linear-gradient(100deg,var(--orange) 0%,#e34c3a 45%,#d52055 80%,#cf1857 100%)}
.speakers h2{position:absolute;top:36px;width:100%;text-align:center;color:var(--white);font-size:21px;font-weight:700}
.rule{position:absolute;left:466px;top:69px;width:38px;height:2px;background:var(--white)}
.avatar{top:680px;width:115px;height:115px;border-radius:50%;background:radial-gradient(circle at 50% 40%,#c9b4a3,#6d7c88)}
.sp{top:686px;width:140px;color:var(--white)}
.sp h3{font-size:18px;font-weight:700}
.sp h4{font-size:10.5px;font-weight:700;margin-top:2px}
.sp p{font-size:9.8px;line-height:1.42;margin-top:10px}
.skyline{left:0;top:862px;width:983px;height:70px;background:linear-gradient(180deg,rgba(255,255,255,0) 0%,rgba(240,240,240,.9) 60%,#eeeeee 100%)}
/* footer */
.footer{left:0;top:925px;width:983px;height:233px;background:linear-gradient(180deg,#ececec,#fff)}
.loc h5{font-size:12px;font-weight:600;color:var(--navy);display:flex;align-items:center;gap:6px}
.loc p{font-size:9px;color:#444;line-height:1.65;margin-top:2px}
.mail{font-size:12px;font-weight:600;color:var(--navy);display:flex;align-items:center;gap:5px}
.bottom{left:0;top:1158px;width:983px;height:42px;background:var(--dark);color:var(--white);font-size:7.5px;font-weight:600}
.bottom a{position:absolute;top:18px;color:var(--white);text-decoration:none}
</style>
</head>
<body>

<nav class="abs topnav">
  <a style="left:67px">HOME</a><a style="left:122px">SOBRE NÓS</a><a style="left:205px">PORTIFÓLIO</a><a style="left:288px">IMÓVEIS</a><a style="left:355px">NOTÍCIAS</a><a style="left:428px">EBOOKS</a><a style="left:494px">CONTATO</a>
  <span class="social" style="left:843px"></span><span class="social" style="left:867px"></span><span class="social" style="left:892px"></span>
</nav>

<header class="abs header">
  <div class="abs phone-pill" style="left:117px;top:15px;width:146px;height:22px;font-size:11px;padding-left:8px">
    <svg width="12" height="12" viewBox="0 0 24 24"><path fill="#fff" d="M6.6 10.8a15 15 0 0 0 6.6 6.6l2.2-2.2c.3-.3.7-.4 1-.2 1.1.4 2.3.6 3.6.6.6 0 1 .4 1 1V20c0 .6-.4 1-1 1A17 17 0 0 1 3 4c0-.6.4-1 1-1h3.5c.6 0 1 .4 1 1 0 1.3.2 2.5.6 3.6.1.3 0 .7-.2 1z"/></svg>EUA +(406) 555-0192</div>
  <div class="abs phones" style="left:76px;top:46px"><span><i class="dot" style="background:var(--green)"></i>+55 21 5550-4417</span><span><i class="dot" style="background:#3b5bb5"></i>+1 (855)555-0178</span></div>
  <div class="abs logo-notch" style="top:59px"></div>
  <div class="abs brand" style="left:391px;top:16px;width:200px;font-size:26px">MAPLE<small style="font-size:14px;margin-top:6px">HEARTH</small></div>
  <div class="abs cta" style="left:643px;top:22px;font-size:10px"><span class="ic" style="width:32px;height:32px;background:var(--magenta)"><svg width="16" height="14" viewBox="0 0 16 14"><rect x="1" y="1" width="14" height="9" rx="2" fill="none" stroke="#fff" stroke-width="1.5"/><path d="M4 10l-1 3 4-3" fill="#fff"/></svg></span>FALE COM UM<br>AGENTE</div>
  <div class="abs cta" style="left:779px;top:22px;font-size:10px"><span class="ic" style="width:32px;height:32px;background:var(--teal)"><svg width="16" height="16" viewBox="0 0 16 16"><rect x="1.5" y="3" width="13" height="11" rx="1.5" fill="none" stroke="#fff" stroke-width="1.5"/><path d="M1.5 6.5h13M5 1.5v3M11 1.5v3" stroke="#fff" stroke-width="1.5"/></svg></span>AGENDE UMA<br>CONVERSA</div>
</header>

<div class="abs hero" role="img" aria-label="Photo of two colleagues smiling while working together at a café table"></div>
<div class="abs hero-shade"></div>
<div class="abs logo-notch" style="left:415px;top:113px;height:28px"></div>

<h1 class="abs title">Augiat in pede fusce<br>tellus sed metus augue</h1>
<div class="abs pill" style="top:313px"><span class="ic"><svg width="16" height="16" viewBox="0 0 16 16"><rect x="1.5" y="3" width="13" height="11" rx="1.5" fill="none" stroke="#fff" stroke-width="1.5"/><path d="M1.5 6.5h13M5 1.5v3M11 1.5v3" stroke="#fff" stroke-width="1.5"/></svg></span>Friday, 17 March 2020</div>
<div class="abs pill" style="top:364px"><span class="ic"><svg width="16" height="16" viewBox="0 0 16 16"><circle cx="8" cy="8" r="6.5" fill="none" stroke="#fff" stroke-width="1.5"/><path d="M8 4v4H5" fill="none" stroke="#fff" stroke-width="1.5"/></svg></span>10: 00 am to 01:00 pm</div>
<div class="abs count" style="left:95px"><b>10</b><span>DAYS</span></div>
<div class="abs count" style="left:159px"><b>08</b><span>HOUR</span></div>
<div class="abs count" style="left:223px"><b>10</b><span>MIN</span></div>
<div class="abs count" style="left:288px"><b>55</b><span>SEC</span></div>
<div class="abs free-tab">All Webinar are Free</div>

<form class="abs form">
  <h2>REGISTERATION NOW</h2>
  <div class="field" style="top:64px">First Name</div>
  <div class="field" style="top:105px">Last Name</div>
  <div class="field" style="top:145px">Email address</div>
  <div class="field" style="top:186px">Phone</div>
  <div class="field" style="top:226px">Company</div>
  <div class="btn">REGISTER</div>
</form>

<section class="abs speakers"><h2>KEYNOTE SPEAKERS</h2><div class="rule"></div></section>
<div class="abs avatar" style="left:100px" role="img" aria-label="Portrait photo of speaker Marco Lindell"></div>
<div class="abs sp" style="left:225px"><h3>Marco Lindell</h3><h4>Subject Title</h4><p>Curabitur vel dolor ultrices ipsum dictum tristique Praesent vitae lacus Ut velit enim vestibulum</p></div>
<div class="abs avatar" style="left:382px" role="img" aria-label="Portrait photo of speaker Omar Castell"></div>
<div class="abs sp" style="left:507px"><h3>Omar Castell</h3><h4>Subject Title</h4><p>Curabitur vel dolor ultrices ipsum dictum tristique Praesent vitae lacus Ut velit enim vestibulum</p></div>
<div class="abs avatar" style="left:663px" role="img" aria-label="Portrait photo of speaker Helena"></div>
<div class="abs sp" style="left:788px"><h3>Helena</h3><h4>Subject Title</h4><p>Curabitur vel dolor ultrices ipsum dictum tristique Praesent vitae lacus Ut velit enim vestibulum</p></div>

<footer class="abs footer"></footer>
<div class="abs skyline" role="img" aria-label="City skyline silhouette illustration"></div>

<div class="abs loc" style="left:101px;top:947px"><h5><svg width="8" height="11" viewBox="0 0 8 11"><path d="M4 0a4 4 0 0 1 4 4c0 3-4 7-4 7S0 7 0 4a4 4 0 0 1 4-4z" fill="var(--magenta)"/><circle cx="4" cy="4" r="1.5" fill="#fff"/></svg>Atlântica Centro</h5><p>3º Piso ao lado do Café Nuvem Av. das Palmeiras 4210,<br>Jardim Azul - RJ - Brasil</p></div>
<div class="abs loc" style="left:101px;top:1006px"><h5><svg width="8" height="11" viewBox="0 0 8 11"><path d="M4 0a4 4 0 0 1 4 4c0 3-4 7-4 7S0 7 0 4a4 4 0 0 1 4-4z" fill="var(--magenta)"/><circle cx="4" cy="4" r="1.5" fill="#fff"/></svg>Shopping Vale Verde</h5><p>Av. Das Acácias, 3120 105/106 Alto da<br>Serra - São Paulo - Brasil</p></div>
<div class="abs loc" style="left:101px;top:1065px"><h5><svg width="8" height="11" viewBox="0 0 8 11"><path d="M4 0a4 4 0 0 1 4 4c0 3-4 7-4 7S0 7 0 4a4 4 0 0 1 4-4z" fill="var(--magenta)"/><circle cx="4" cy="4" r="1.5" fill="#fff"/></svg>Lakeside</h5><p>4820 Harbor Point Avenue, Suite 210, Lakeside, EUA</p></div>
<div class="abs mail" style="left:101px;top:1105px"><svg width="13" height="10" viewBox="0 0 13 10"><rect width="13" height="10" rx="1" fill="var(--magenta)"/><path d="M0 1l6.5 5L13 1" fill="none" stroke="#fff" stroke-width="1.2"/></svg>Contact@Themaplehearth.Com</div>

<div class="abs brand" style="left:371px;top:970px;width:200px;font-size:30px">MAPLE<small style="font-size:15px;margin-top:6px">HEARTH</small></div>

<div class="abs phone-pill" style="left:634px;top:946px;width:185px;height:25px;font-size:13px;padding-left:8px"><svg width="13" height="13" viewBox="0 0 24 24"><path fill="#fff" d="M6.6 10.8a15 15 0 0 0 6.6 6.6l2.2-2.2c.3-.3.7-.4 1-.2 1.1.4 2.3.6 3.6.6.6 0 1 .4 1 1V20c0 .6-.4 1-1 1A17 17 0 0 1 3 4c0-.6.4-1 1-1h3.5c.6 0 1 .4 1 1 0 1.3.2 2.5.6 3.6.1.3 0 .7-.2 1z"/></svg>EUA +(406) 555-0192</div>
<div class="abs phones" style="left:621px;top:979px;font-size:10px"><span><i class="dot" style="background:var(--green)"></i>+55 21 5550-4417</span><span><i class="dot" style="background:#3b5bb5"></i>+1 (855)555-0178</span></div>
<div class="abs cta" style="left:610px;top:1013px;font-size:11px"><span class="ic" style="width:28px;height:28px;background:var(--magenta)"><svg width="14" height="12" viewBox="0 0 16 14"><rect x="1" y="1" width="14" height="9" rx="2" fill="none" stroke="#fff" stroke-width="1.5"/><path d="M4 10l-1 3 4-3" fill="#fff"/></svg></span>FALE COM UM<br>AGENTE</div>
<div class="abs cta" style="left:727px;top:1013px;font-size:11px"><span class="ic" style="width:28px;height:28px;background:var(--teal)"><svg width="14" height="14" viewBox="0 0 16 16"><rect x="1.5" y="3" width="13" height="11" rx="1.5" fill="none" stroke="#fff" stroke-width="1.5"/><path d="M1.5 6.5h13M5 1.5v3M11 1.5v3" stroke="#fff" stroke-width="1.5"/></svg></span>AGENDE UMA<br>CONVERSA</div>

<div class="abs bottom">
  <span class="abs" style="left:101px;top:18px">© 2017 - THE MAPLE HEARTH BY <span style="color:var(--magenta);font-weight:400">NORTHPIXEL</span></span>
  <a style="left:563px;color:var(--magenta);font-weight:400">HOME</a><a style="left:611px">IMÓVEIS</a><a style="left:667px">NOTÍCIAS</a><a style="left:728px">CONTATO</a><a style="left:791px">TERMS OF USE</a>
</div>

</body>
</html>
```